Executive Performance Review mapped on J-curve

I need to turn an executive company performance review into a visual infographic. The list of accomplishments is grouped into four calendar quarters. Each quarter needs a subtle representation of the season. The four quarters and associated list of accomplishments need to be mapped to a J-curve. - Spreadsheet with accomplishments attached (Marlowbend)- Sample image of a J-curve. You can google J-curve to see more images.- The title should be "Danica Ostrander Year in Review"

Target Market(s)

Board of Directors

Requirements
Nice to have
• This will be presented to a company founder that is an artist and customer experience expert. He is very visual so a nice visual representation of the data will be impactful. He also uses the phrase that you have to live with or work with someone for four seasons before you really know them. This is why I have the seasons mapped to the quarters. The Fall season motif should be gloomy and stormy.

```html
<!DOCTYPE html>
<html lang="en">
<head>
<meta charset="utf-8">
<title>Danica Ostrander – Year One In Review</title>
<link rel="stylesheet" href="https://fonts.googleapis.com/css2?family=Montserrat:wght@500;800&family=Source+Sans+3:wght@400;700&display=swap">
<style>
  :root {
    --ink: #2e2e2e;
    --title: #3a3a3a;
    --summer-bg: #fdf9d8;
    --fall-bg: #c6e2e7;
    --winter-bg: #eefafb;
    --spring-bg: #f3f8dc;
    --future-bg: #e1f1ea;
    --summer-bar: #f8c81c;
    --fall-bar: #4b5660;
    --winter-bar: #ffffff;
    --spring-bar: #bddc58;
    --future-bar: #2f7d33;
  }
  * { margin: 0; padding: 0; box-sizing: border-box; }
  html, body { width: 1200px; height: 706px; overflow: hidden; background: #fff; }
  .canvas { position: relative; width: 1200px; height: 706px; font-family: "Source Sans 3", "Segoe UI", sans-serif; color: var(--ink); }

  .header { position: absolute; top: 34px; left: 0; width: 1200px; text-align: center; color: var(--title); }
  .header__name { font-family: "Montserrat", sans-serif; font-weight: 800; font-size: 31px; letter-spacing: -0.3px; line-height: 36px; }
  .header__date { font-family: "Montserrat", sans-serif; font-weight: 500; font-size: 25px; line-height: 30px; margin-top: 2px; }
  .header__company { font-family: "Montserrat", sans-serif; font-weight: 500; font-size: 19px; line-height: 24px; margin-top: 2px; }

  .season { position: absolute; top: 142px; height: 540px; }
  .season--summer { left: 34px; width: 228px; background: var(--summer-bg); }
  .season--fall { left: 262px; width: 228px; background: var(--fall-bg); }
  .season--winter { left: 490px; width: 227px; background: var(--winter-bg); }
  .season--spring { left: 717px; width: 227px; background: var(--spring-bg); }
  .season--future { left: 944px; width: 228px; background: var(--future-bg); }

  .jcurve { position: absolute; left: 34px; top: 142px; width: 1138px; height: 540px; }

  .notes { position: absolute; top: 149px; padding-left: 7px; padding-right: 6px; font-size: 10.4px; line-height: 14.5px; }
  .notes h3 { font-size: 10.4px; font-weight: 700; margin-top: 10px; }
  .notes h3:first-child { margin-top: 0; }
  .notes ul { list-style: none; }
  .notes li::before { content: "• "; }
  .notes p { }
  .notes--summer { left: 34px; width: 228px; }
  .notes--fall { left: 262px; width: 228px; }
  .notes--winter { left: 490px; width: 227px; }
  .notes--spring { left: 717px; width: 227px; }
  .notes--future { left: 960px; width: 200px; }

  .label { position: absolute; top: 666px; height: 16px; font-size: 10px; font-weight: 700; line-height: 16px; text-align: center; }
  .label--summer { left: 34px; width: 228px; background: var(--summer-bar); color: #3a2b00; }
  .label--fall { left: 262px; width: 228px; background: var(--fall-bar); color: #e8ecef; }
  .label--winter { left: 490px; width: 227px; background: var(--winter-bar); color: #2a2a2a; }
  .label--spring { left: 717px; width: 227px; background: var(--spring-bar); color: #2b3a10; }
  .label--future { left: 944px; width: 228px; background: var(--future-bar); color: #eaf6ea; }
</style>
</head>
<body>
<div class="canvas">
  <header class="header">
    <h1 class="header__name">DANICA OSTRANDER - YEAR ONE IN</h1>
    <p class="header__date">JULY 1, 2019 REVIEW</p>
    <p class="header__company">HALVERN WORKS, INC.</p>
  </header>

  <div class="season season--summer"></div>
  <div class="season season--fall"></div>
  <div class="season season--winter"></div>
  <div class="season season--spring"></div>
  <div class="season season--future"></div>

  <svg class="jcurve" viewBox="0 0 1138 540" role="img" aria-label="J-curve landscape: sunny beach with palms, stormy rainy fall, snowy winter with snowflakes, flowering spring meadow with butterflies and a bird, rising into green growth">
    <defs>
      <linearGradient id="seasonGround" x1="0" y1="0" x2="1" y2="0">
        <stop offset="0" stop-color="#f9d21e"/>
        <stop offset="0.18" stop-color="#f3cc2a"/>
        <stop offset="0.22" stop-color="#6a737b"/>
        <stop offset="0.38" stop-color="#858d94"/>
        <stop offset="0.44" stop-color="#d4f1f8"/>
        <stop offset="0.6" stop-color="#c8edf6"/>
        <stop offset="0.68" stop-color="#d7ec9a"/>
        <stop offset="0.8" stop-color="#b6da5c"/>
        <stop offset="0.9" stop-color="#5ea843"/>
        <stop offset="1" stop-color="#2f7d33"/>
      </linearGradient>
    </defs>
    <path d="M0 388 C 160 420, 320 455, 450 454 C 700 440, 950 230, 1138 0 L 1138 540 L 0 540 Z" fill="url(#seasonGround)"/>
  </svg>

  <section class="notes notes--summer">
    <h3>TRANSITIONS</h3>
    <ul>
      <li>RO Transition from Rolf &amp; Inez</li>
      <li>Start CR Office Initiative</li>
      <li>Tactical Ops transition from Rolf</li>
      <li>Formalize Exec Team</li>
    </ul>
    <h3>BIZ ARCHITECTURE</h3>
    <ul>
      <li>Independent Financial Audit</li>
      <li>Organizational Audit - Structure</li>
      <li>Organizational Audit - People</li>
      <li>XF Framework - ESU</li>
      <li>Defined Utilization, Realization, Availability</li>
    </ul>
    <h3>STRATEGY</h3>
    <ul>
      <li>Effective Strategy Meeting</li>
      <li>Strategic Themes 2018 - 2020: Stablize, Accel-erate, Surge</li>
      <li>Business Drivers: Drive Revenue, Improve</li>
      <li>Halverner Experience, Increase Brand Awareness</li>
    </ul>
    <h3>SALES</h3>
    <ul>
      <li>Tallis Account Transition</li>
      <li>Norwell Account Transition</li>
      <li>2 year Managed Services Engagement Model</li>
    </ul>
    <h3>REVENUE / EBITA</h3>
    <ul><li>TBD</li></ul>
  </section>

  <section class="notes notes--fall">
    <h3>BIZ ARCHITECTURE</h3>
    <ul>
      <li>XF Framework - Functional Meetings &amp;</li>
      <li>Scrum of Scrums</li>
      <li>Structured Reorg</li>
      <li>Implemented Reorg</li>
      <li>Quarterly Org Iteration cadence</li>
      <li>Defined Key Hire Plan</li>
      <li>CR Office Operational</li>
      <li>Time Accountability</li>
      <li>Tools ReConfig</li>
      <li>Org Structure v1</li>
    </ul>
    <h3>STRATEGY</h3>
    <ul><li>Internal QBR Accountability</li></ul>
    <h3>SALES</h3>
    <ul>
      <li>Brightwell QBR</li>
      <li>Tallis QBR</li>
    </ul>
    <h3>REVENUE / EBITA</h3>
    <ul><li>TBD</li></ul>
  </section>

  <section class="notes notes--winter">
    <h3>BIZ ARCHITECTURE</h3>
    <ul>
      <li>XF Framework - Progress Demos</li>
      <li>Org Structure - COE's</li>
      <li>Stablize Accounting &amp; Finance</li>
      <li>Exec Hiring Process</li>
    </ul>
    <h3>KEY HIRES</h3>
    <ul>
      <li>Controller</li>
      <li>Director CX</li>
    </ul>
    <h3>STRATEGY</h3>
    <ul>
      <li>Founders removed from front line activity</li>
      <li>Halvern QBR - Goal Setting &amp; Tracking</li>
    </ul>
    <h3>SALES</h3>
    <p>Norwell QBR</p>
    <p>Tallis QBR</p>
    <h3>REVENUE / EBITA</h3>
    <p>TBD</p>
  </section>

  <section class="notes notes--spring">
    <h3>BIZ ARCHITECTURE</h3>
    <ul>
      <li>Tiered Pricing Pre-Paid Engagement Model</li>
      <li>XF Framework - Ideation Board</li>
      <li>Consulting Levels &amp; Salary Bands</li>
      <li>Roles &amp; Responsibilities</li>
    </ul>
    <h3>KEY HIRES</h3>
    <ul>
      <li>Interim HR</li>
      <li>Provisional Client Partner</li>
      <li>Acting Director 1</li>
      <li>Acting Director 2</li>
      <li>Client Partner 1</li>
      <li>Sales Exec 1</li>
    </ul>
    <h3>SALES</h3>
    <ul>
      <li>Opened Cloudframe Door</li>
      <li>Flipped focus from operationaly run company to sales/marketing driven org</li>
      <li>Parkline Direct</li>
    </ul>
    <h3>REVENUE / EBITA</h3>
    <ul><li>TBD</li></ul>
  </section>

  <section class="notes notes--future">
    <h3>• GREENFIELD</h3>
  </section>

  <div class="label label--summer">SUMMER: Q3 2018 - ASSESSMENT</div>
  <div class="label label--fall">FALL: Q4 2018 - STABLIZE</div>
  <div class="label label--winter">WINTER: Q1 2019 - STRATACTICAL</div>
  <div class="label label--spring">SPRING: Q2 2019 - STRATEGIC</div>
  <div class="label label--future">2020+: VALUE CREATION</div>
</div>
</body>
</html>
```